Tech business card design

We need an amazing business card design for our new business 'Pexla' a marketing tech startup based in Sydney, Australia. We provide an online marketplace for businesses to search and buy advertising media, connect with service providers and learn more about marketing. We wish to communicate 'cool tech', reliability and professionalism and design based around our logo.

Target Market(s)

Business Owners

Contact Information for Business Card

Name
Position
Email Address
Website
Phone Number

Font styles to use
Other font styles liked:
• Avenir & Avenir Next

Colors

Designer to choose colors to be used in the design.

```html
<!DOCTYPE html>
<html lang="en">
<head>
<meta charset="utf-8">
<title>Pexla Business Card</title>
<link rel="stylesheet" href="https://fonts.googleapis.com/css2?family=Arimo:wght@400;700&display=swap">
<style>
  :root {
    --backdrop: #2a2a2d;
    --navy: #141a4b;
    --grey: #8c8c8e;
    --white: #ffffff;
    --ink: #1c1c1c;
    --logo-faint: #6a6e98;
  }
  * { box-sizing: border-box; margin: 0; padding: 0; }
  html, body {
    width: 1200px;
    height: 803px;
    overflow: hidden;
    background: var(--backdrop);
    font-family: "Arimo", Arial, sans-serif;
  }
  .stage {
    width: 1200px;
    height: 803px;
    display: flex;
    align-items: center;
    justify-content: center;
    gap: 50px;
  }
  .card {
    position: relative;
    width: 525px;
    height: 300px;
    overflow: hidden;
    box-shadow: 0 14px 30px rgba(0,0,0,0.45);
  }
  .card-front { background: var(--white); }
  .card-back { background: var(--navy); display: flex; align-items: center; justify-content: center; }

  .swoosh { position: absolute; inset: 0; width: 100%; height: 100%; }

  .wordmark {
    position: absolute;
    left: 42px;
    top: 42px;
    font-weight: 700;
    font-size: 78px;
    letter-spacing: -2px;
    line-height: 1;
    color: var(--navy);
  }
  .contact {
    position: absolute;
    left: 60px;
    top: 150px;
    font-size: 12.5px;
    color: var(--ink);
    line-height: 1.25;
  }
  .contact-address { margin-bottom: 10px; }
  .contact-address span { display: block; }
  .contact-address span + span { padding-left: 10px; }
  .contact-line {
    display: flex;
    align-items: center;
    gap: 5px;
    margin-top: 5px;
    padding-left: 8px;
  }
  .contact-line svg { width: 11px; height: 11px; fill: var(--ink); flex: none; }

  .holder {
    position: absolute;
    right: 30px;
    top: 148px;
    text-align: right;
    color: var(--white);
    font-weight: 700;
  }
  .holder-name { font-size: 15px; letter-spacing: 0.3px; }
  .holder-role { font-size: 11.5px; margin-top: 2px; }

  .wordmark-back {
    font-weight: 700;
    font-size: 120px;
    letter-spacing: -3px;
    line-height: 1;
    color: var(--logo-faint);
  }
</style>
</head>
<body>
<main class="stage">
  <section class="card card-front" aria-label="Card front">
    <svg class="swoosh" viewBox="0 0 525 300" preserveAspectRatio="none" aria-hidden="true">
      <path fill="var(--grey)" d="M430 0 C400 60 390 140 330 190 C260 245 130 262 0 262 L0 300 L525 300 L525 0 Z"/>
      <path fill="var(--white)" d="M442 0 C414 62 404 146 342 198 C270 255 135 272 0 272 L0 300 L525 300 L525 0 Z"/>
      <path fill="var(--navy)" d="M456 0 C428 64 418 150 354 204 C282 262 140 278 0 278 L0 300 L525 300 L525 0 Z"/>
      <path fill="var(--grey)" d="M0 286 C130 292 250 284 370 252 C280 290 150 300 0 300 Z"/>
      <path fill="var(--white)" d="M0 294 C110 298 210 296 290 286 C220 300 120 300 0 300 Z"/>
    </svg>

    <div class="wordmark">pexla</div>

    <div class="contact">
      <p class="contact-address"><span>Street Name, City Name</span><span>Zipcode:012345</span></p>
      <p class="contact-line">
        <svg viewBox="0 0 24 24"><path d="M6.6 10.8a15 15 0 0 0 6.6 6.6l2.2-2.2a1 1 0 0 1 1-.25 11.4 11.4 0 0 0 3.6.6 1 1 0 0 1 1 1V20a1 1 0 0 1-1 1A17 17 0 0 1 3 4a1 1 0 0 1 1-1h3.5a1 1 0 0 1 1 1c0 1.25.2 2.45.6 3.6a1 1 0 0 1-.25 1z"/></svg>
        012-345-6789
      </p>
      <p class="contact-line">
        <svg viewBox="0 0 24 24"><path d="M2 5h20v14H2z M4 7v.5l8 5.5 8-5.5V7z" fill-rule="evenodd"/></svg>
        info@pexla.com
      </p>
      <p class="contact-line">
        <svg viewBox="0 0 24 24"><path d="M12 2a10 10 0 1 0 0 20 10 10 0 0 0 0-20zm0 2c1 0 2.3 2 2.8 5H9.2C9.7 6 11 4 12 4zm-4.8 5H4.6a8 8 0 0 1 4-4.4A13 13 0 0 0 7.2 9zm0 2c-.1.7-.1 1.3-.1 2h-3a8 8 0 0 1 .1-2zm2 0h5.6a14 14 0 0 1 0 2H9.2a14 14 0 0 1 0-2zm7.6 0h3a8 8 0 0 1 0 2h-3zm-.8-2a13 13 0 0 0-1.4-4.4 8 8 0 0 1 4 4.4zM4.6 15h2.6a13 13 0 0 0 1.4 4.4 8 8 0 0 1-4-4.4zm4.6 0h5.6c-.5 3-1.8 5-2.8 5s-2.3-2-2.8-5zm7.6 0h2.6a8 8 0 0 1-4 4.4 13 13 0 0 0 1.4-4.4z"/></svg>
        www.pexla.com
      </p>
    </div>

    <div class="holder">
      <p class="holder-name">JOHN SMITH</p>
      <p class="holder-role">Position</p>
    </div>
  </section>

  <section class="card card-back" aria-label="Card back">
    <div class="wordmark-back">pexla</div>
  </section>
</main>
</body>
</html>
```